Business Card Design for Marketing Firm

Looking for business card design for higher end marketing firm. Clean but impressionable/trendy. We are a marketing firm that represents manufacturers in the foodservice equipment and supply industry. Our customers are end users such has hotels, restaurants, country clubs, convention centers and casinos as well as distributors of restaurants supplies and equipment, and manufacturers of foodservice equipment and supplies.
Target Market(s)
Hotels, Restaurants, Supply & Equipment Distributors, Foodservice Manufacturers
Industry/Entity Type
Foodservice/Hospitality
Contact Information for Business Card
Name, Title, Contact Number, Email, Website, Social Media, Address
Requirements
Must have
- Clean & Simple but Serious and Impressionable

```html
<!DOCTYPE html>
<html lang="en">
<head>
<meta charset="utf-8">
<title>Harbor Table Reps – Business Card</title>
<link href="https://fonts.googleapis.com/css2?family=Open+Sans:wght@400;600;700&display=swap" rel="stylesheet">
<style>
  :root {
    --navy: #23257a;
    --navy-deep: #1e2068;
    --navy-emboss: #2c2f8c;
    --ink: #2b2b2b;
    --paper: #ffffff;
    --backdrop: #e9e9ec;
  }
  * { box-sizing: border-box; margin: 0; padding: 0; }
  html, body { width: 1200px; height: 786px; overflow: hidden; }
  body {
    background: var(--backdrop);
    font-family: "Open Sans", Arial, sans-serif;
    position: relative;
  }
  .card {
    position: absolute;
    top: 238px;
    width: 540px;
    height: 309px;
    box-shadow: 0 6px 18px rgba(0,0,0,.18);
  }
  .card-front { left: 40px; background: var(--paper); }
  .card-back { left: 620px; background: var(--navy); display: flex; align-items: center; justify-content: center; }

  .brand {
    position: absolute;
    left: 34px; top: 118px;
    width: 230px;
    display: flex; align-items: center; gap: 10px;
  }
  .brand-dot { width: 14px; height: 14px; border-radius: 50%; background: var(--navy); flex: none; }
  .brand-name { font-weight: 700; font-size: 21px; color: var(--navy); letter-spacing: .5px; line-height: 1.15; text-transform: uppercase; }

  .divider { position: absolute; left: 282px; top: 46px; width: 2px; height: 160px; background: var(--navy); }

  .contact { position: absolute; left: 304px; top: 40px; color: var(--ink); }
  .person-name { font-weight: 700; font-size: 19px; color: var(--navy); letter-spacing: .3px; line-height: 1.1; }
  .person-title { font-size: 12.5px; color: var(--ink); margin-top: 2px; }
  .contact-list { list-style: none; margin-top: 12px; }
  .contact-list li { display: flex; align-items: center; gap: 7px; font-size: 13px; line-height: 21px; }
  .contact-list svg { width: 13px; height: 13px; fill: var(--navy); flex: none; }
  .address { font-size: 13px; line-height: 18px; margin-top: 12px; padding-left: 20px; }

  .follow { position: absolute; left: 304px; bottom: 36px; display: flex; align-items: center; gap: 12px; }
  .follow-label { font-weight: 700; font-size: 21px; color: var(--navy); }
  .social { display: flex; gap: 4px; }
  .social span { width: 16px; height: 16px; border-radius: 50%; background: var(--navy); }

  .back-brand { display: flex; align-items: center; gap: 14px; }
  .back-brand .brand-dot { width: 20px; height: 20px; background: var(--navy-emboss); }
  .back-brand .brand-name { font-size: 32px; color: var(--navy-emboss); }
</style>
</head>
<body>
  <section class="card card-front" aria-label="Business card front">
    <div class="brand">
      <span class="brand-dot"></span>
      <span class="brand-name">Harbor Table Reps</span>
    </div>
    <div class="divider"></div>
    <div class="contact">
      <p class="person-name">DANIEL REED</p>
      <p class="person-title">Managing Director</p>
      <ul class="contact-list">
        <li><svg viewBox="0 0 24 24" aria-hidden="true"><path d="M6.6 10.8a15.1 15.1 0 0 0 6.6 6.6l2.2-2.2a1 1 0 0 1 1-.25 11.4 11.4 0 0 0 3.6.57 1 1 0 0 1 1 1V20a1 1 0 0 1-1 1A17 17 0 0 1 3 4a1 1 0 0 1 1-1h3.5a1 1 0 0 1 1 1c0 1.25.2 2.45.57 3.57a1 1 0 0 1-.25 1z"/></svg>123 456 789</li>
        <li><svg viewBox="0 0 24 24" aria-hidden="true"><path d="M2 5h20v14H2zm2 2v.4l8 5 8-5V7zm0 2.8V17h16V9.8l-8 5z"/></svg>info@yourmail.com</li>
        <li><svg viewBox="0 0 24 24" aria-hidden="true"><path d="M12 2a10 10 0 1 0 0 20 10 10 0 0 0 0-20zm-1 17.9A8 8 0 0 1 4.1 11H7c.1 3 .9 6 4 8.9zM7 9H4.3A8 8 0 0 1 11 4.1C8 7 7.2 9 7 9zm2 0c.3-2 1.2-3.6 3-5.2 1.8 1.6 2.7 3.2 3 5.2zm0 2h6c-.2 2.8-1.2 5.2-3 7.1-1.8-1.9-2.8-4.3-3-7.1zm4 8.9c3.1-2.9 3.9-5.9 4-8.9h2.9a8 8 0 0 1-6.9 8.9zM17 9c-.2 0-1-2-4-4.9A8 8 0 0 1 19.7 9z"/></svg>www.yourwebsite.com</li>
      </ul>
      <p class="address">Your address, City<br>State, Zip 1234</p>
    </div>
    <div class="follow">
      <span class="follow-label">Follow Us</span>
      <div class="social" aria-hidden="true"><span></span><span></span><span></span><span></span><span></span><span></span></div>
    </div>
  </section>

  <section class="card card-back" aria-label="Business card back">
    <div class="back-brand">
      <span class="brand-dot"></span>
      <span class="brand-name">Harbor Table Reps</span>
    </div>
  </section>
</body>
</html>
```